Need a business card design for a residential architect.

You can get a sense of his work at www.tberlove.com

Would like a consistent look and feel between business card and website
.

Target Market(s)

Residential homeowners builders

Industry/Entity Type

Residential

Contact Information for Business Card

Dale Morrick
Principle
Morrick Architecture
418 Kestrel Lane
Menlo Park, CA 94025

dale@tberlove.com

tberlove.com
phone: 650-555-2716
Fax: 650-555-8043

Font styles to use
Sans Serif

Requirements
Must have
• Details above
Nice to have
• Would like a consistent look and feel between business card and website
Should not have
• None

```html
<!DOCTYPE html>
<html lang="en">
<head>
<meta charset="utf-8">
<title>Morrick Architecture – Business Card</title>
<link rel="stylesheet" href="https://fonts.googleapis.com/css2?family=Open+Sans:wght@400;700&display=swap">
<style>
  :root {
    --bg: #ececec;
    --card: #f7f7f7;
    --ink: #1f1f1f;
    --muted: #555555;
    --brand-grey: #8a8a8a;
    --edge-grey: #9c9c9c;
    --rule: #444444;
  }
  * { box-sizing: border-box; margin: 0; padding: 0; }
  html, body {
    width: 1200px; height: 1001px; overflow: hidden;
    background: var(--bg);
    font-family: "Open Sans", Arial, sans-serif;
    color: var(--ink);
  }
  .sheet {
    width: 1200px; height: 1001px;
    display: flex; align-items: center; justify-content: center; gap: 40px;
  }
  .card {
    position: relative;
    width: 540px; height: 309px;
    background: var(--card);
    border-left: 10px solid var(--edge-grey);
    box-shadow: 0 2px 10px rgba(0,0,0,0.12);
  }
  .wordmark {
    font-family: "Open Sans", Arial, sans-serif;
    font-weight: 400;
    color: var(--brand-grey);
    text-transform: uppercase;
    line-height: 1.15;
    text-align: center;
  }
  /* Contact side */
  .contact .person { position: absolute; left: 26px; top: 30px; }
  .contact .person-name { font-size: 15px; font-weight: 700; }
  .contact .person-title { font-size: 11px; color: var(--muted); }
  .contact .divider {
    position: absolute; left: 0; top: 80px; width: 300px;
    border-top: 1px solid var(--rule);
  }
  .contact .details {
    position: absolute; left: 26px; top: 92px;
    list-style: none; font-size: 12px; line-height: 20px;
  }
  .contact .details li { display: flex; align-items: center; gap: 10px; }
  .contact .details svg { width: 12px; height: 12px; fill: var(--muted); flex: none; }
  .contact .wordmark {
    position: absolute; right: 34px; top: 92px;
    font-size: 20px; letter-spacing: 3px;
  }
  .contact .web {
    position: absolute; right: 34px; bottom: 30px;
    display: flex; align-items: center; gap: 8px; font-size: 12px;
  }
  .contact .web svg { width: 14px; height: 14px; }
  /* Brand side */
  .brand { display: flex; align-items: center; justify-content: center; }
  .brand .wordmark { font-size: 32px; letter-spacing: 5px; }
</style>
</head>
<body>
<main class="sheet">
  <section class="card contact" aria-label="Card contact side">
    <div class="person">
      <p class="person-name">Dale Morrick</p>
      <p class="person-title">Principle</p>
    </div>
    <hr class="divider">
    <ul class="details">
      <li><svg viewBox="0 0 12 12"><path d="M6 0a4 4 0 0 0-4 4c0 3 4 8 4 8s4-5 4-8a4 4 0 0 0-4-4zm0 5.5A1.5 1.5 0 1 1 6 2.5a1.5 1.5 0 0 1 0 3z"/></svg>418 Kestrel Lane Menlo Park, CA 94025</li>
      <li><svg viewBox="0 0 12 12"><path d="M0 2h12v8H0z M0 2l6 4.5L12 2" stroke="#f7f7f7" stroke-width="0.8"/></svg>dale@tberlove.com</li>
      <li><svg viewBox="0 0 12 12"><path d="M1 4c0-2 2-3 5-3s5 1 5 3H8.5V3h-5v1zM2 6h8l1 5H1z"/></svg>650-555-2716</li>
      <li><svg viewBox="0 0 12 12"><path d="M3 1h6v3H3zM1 5h10v5H9V8H3v2H1zM3 9h6v3H3z"/></svg>650-555-8043</li>
    </ul>
    <p class="wordmark">Morrick<br>Architecture</p>
    <p class="web">
      <svg viewBox="0 0 14 14" fill="none" stroke="#555555" stroke-width="1"><circle cx="7" cy="7" r="6"/><ellipse cx="7" cy="7" rx="2.6" ry="6"/><path d="M1 7h12M2 4h10M2 10h10"/></svg>
      www.tberlove.com
    </p>
  </section>
  <section class="card brand" aria-label="Card brand side">
    <p class="wordmark">Morrick<br>Architecture</p>
  </section>
</main>
</body>
</html>
```